One Thumbnail for Online Shop for PowerPoint Templates needed

We are selling PowerPoint Templates and need therefore a thumbnail for our online shop.

You can use a stock photo, mock-ups or other design elements.

Format:
squared like 500 x 500
or wide like 1280 x 720

If you want to use a title, use:

"Graphs" ---> Title
"PowerPoint template" ---> subtitle

Attachments:
- OLD: Our old thumbnail which I do not like
- Template: PowerPoint pictures which you can use ( you can also copy them if you need more than these)
- Example: Some examples I found from other shops (please do not copy them exactly, only to show what I mean)

I received lots of designs until now but many are not what I have expected

Target Market(s)

E-Commerce

Industry/Entity Type

Shop

Font styles to use
Sans Serif

Requirements
Should not have
• Do NOT re-design one of the template.png (these are only examples, I will replace them later)

```html
<!DOCTYPE html>
<html lang="en">
<head>
<meta charset="utf-8">
<title>Standard Graphs – Template Thumbnail</title>
<link rel="stylesheet" href="https://fonts.googleapis.com/css2?family=Exo:wght@300&family=Quicksand:wght@300&family=Arimo:wght@400;700&display=swap">
<style>
  :root {
    --bg-dark: #2a2018;
    --bg-mid: #4a3b2e;
    --bg-light: #6b5a4a;
    --slide-bg: #f7f9fc;
    --ink: #1c1c1c;
    --muted: #6d7580;
    --bar-light: #4a8fd4;
    --bar-dark: #1f4e7d;
    --grid: #e2e6ea;
    --title: #ffffff;
  }
  * { margin: 0; padding: 0; box-sizing: border-box; }
  html, body { width: 1200px; height: 754px; overflow: hidden; background: var(--bg-dark); }
  .thumbnail { position: relative; width: 1200px; height: 754px; overflow: hidden; }
  .scene-photo {
    position: absolute; inset: 0;
    background:
      radial-gradient(ellipse at 72% 30%, #8a8580 0%, transparent 45%),
      radial-gradient(ellipse at 78% 85%, #5a4a3c 0%, transparent 35%),
      linear-gradient(135deg, var(--bg-dark) 0%, var(--bg-mid) 45%, var(--bg-light) 70%, var(--bg-dark) 100%);
    opacity: 0.9;
  }
  .slide {
    position: absolute; left: 74px; width: 293px; height: 165px;
    background: var(--slide-bg);
    box-shadow: 0 2px 10px rgba(0,0,0,0.35);
  }
  .slide svg { display: block; width: 100%; height: 100%; font-family: 'Arimo', sans-serif; }
  .slide--grid { top: 114px; }
  .slide--combo { top: 315px; }
  .slide--ranking { top: 514px; }
  .headline {
    position: absolute; left: 426px; top: 478px;
    color: var(--title);
    font-family: 'Exo', sans-serif; font-weight: 300;
    font-size: 88px; line-height: 76px; letter-spacing: 4px;
    white-space: nowrap;
  }
  .subline {
    position: absolute; left: 430px; top: 642px;
    color: var(--title);
    font-family: 'Quicksand', sans-serif; font-weight: 300;
    font-size: 41px; letter-spacing: 2.5px;
    white-space: nowrap;
  }
</style>
</head>
<body>
<div class="thumbnail">
  <div class="scene-photo" role="img" aria-label="Darkened photo of a laptop showing charts on a wooden desk with a notebook and a coffee cup"></div>

  <div class="slide slide--grid">
    <svg viewBox="0 0 366 206">
      <defs>
        <g id="mini-chart">
          <line x1="0" y1="0" x2="100" y2="0" stroke="var(--grid)" stroke-width="0.5"/>
          <line x1="0" y1="-20" x2="100" y2="-20" stroke="var(--grid)" stroke-width="0.5"/>
          <line x1="0" y1="-40" x2="100" y2="-40" stroke="var(--grid)" stroke-width="0.5"/>
          <g fill="var(--bar-light)">
            <rect x="4" y="-20" width="4.5" height="20"/><rect x="12" y="-26" width="4.5" height="26"/>
            <rect x="20" y="-30" width="4.5" height="30"/><rect x="28" y="-40" width="4.5" height="40"/>
            <rect x="36" y="-36" width="4.5" height="36"/><rect x="44" y="-34" width="4.5" height="34"/>
            <rect x="52" y="-32" width="4.5" height="32"/><rect x="60" y="-30" width="4.5" height="30"/>
            <rect x="68" y="-26" width="4.5" height="26"/><rect x="76" y="-22" width="4.5" height="22"/>
            <rect x="84" y="-28" width="4.5" height="28"/><rect x="92" y="-28" width="4.5" height="28"/>
          </g>
          <g fill="var(--bar-dark)">
            <rect x="4" y="-12" width="4.5" height="12"/><rect x="12" y="-18" width="4.5" height="18"/>
            <rect x="20" y="-20" width="4.5" height="20"/><rect x="28" y="-20" width="4.5" height="20"/>
            <rect x="36" y="-18" width="4.5" height="18"/><rect x="44" y="-18" width="4.5" height="18"/>
            <rect x="52" y="-20" width="4.5" height="20"/><rect x="60" y="-18" width="4.5" height="18"/>
            <rect x="68" y="-14" width="4.5" height="14"/><rect x="76" y="-12" width="4.5" height="12"/>
            <rect x="84" y="-18" width="4.5" height="18"/><rect x="92" y="-16" width="4.5" height="16"/>
          </g>
          <text x="50" y="5" font-size="3" fill="var(--muted)" text-anchor="middle">Text Text Text Text Text Text Text Text Text Text Text Text</text>
        </g>
        <g id="bullets-3" font-size="3.6" fill="var(--muted)">
          <text y="0">• Lorem ipsum dolor sit</text><text x="4" y="5">amet consetetur elit</text><text x="4" y="10">sed diam nonumy</text><text x="4" y="15">eirmod tempor</text>
        </g>
      </defs>
      <text x="183" y="18" font-size="11" font-weight="700" fill="var(--ink)" text-anchor="middle">Lorem ipsum dolor sit amet</text>
      <text x="183" y="31" font-size="6" fill="var(--ink)" text-anchor="middle">Lorem ipsum dolor sit amet, consectetuer adipiscing elit. Aenean commodo ligula eget dolor.</text>
      <text x="25" y="52" font-size="5" fill="var(--ink)">Lorem ipsum</text>
      <text x="142" y="52" font-size="5" fill="var(--ink)">Lorem ipsum</text>
      <text x="25" y="128" font-size="5" fill="var(--ink)">Lorem ipsum</text>
      <text x="142" y="128" font-size="5" fill="var(--ink)">Lorem ipsum</text>
      <use href="#mini-chart" x="24" y="110"/>
      <use href="#mini-chart" x="141" y="110"/>
      <use href="#mini-chart" x="24" y="186"/>
      <use href="#mini-chart" x="141" y="186"/>
      <use href="#bullets-3" x="272" y="72"/>
      <use href="#bullets-3" x="272" y="114"/>
      <use href="#bullets-3" x="272" y="156"/>
      <text x="350" y="200" font-size="3.5" fill="var(--muted)">31</text>
    </svg>
  </div>

  <div class="slide slide--combo">
    <svg viewBox="0 0 366 206">
      <text x="183" y="18" font-size="11" font-weight="700" fill="var(--ink)" text-anchor="middle">Lorem ipsum dolor sit amet</text>
      <text x="183" y="31" font-size="6" fill="var(--ink)" text-anchor="middle">Lorem ipsum dolor sit amet, consectetuer adipiscing elit. Aenean commodo ligula eget dolor.</text>
      <g font-size="3.8" fill="var(--muted)">
        <text x="20" y="86">• Lorem ipsum dolor sit</text><text x="24" y="92">amet consetetur elit</text><text x="24" y="98">sed diam nonumy</text><text x="24" y="104">eirmod tempor</text>
        <text x="20" y="140">• Lorem ipsum dolor sit</text><text x="24" y="146">amet consetetur elit</text><text x="24" y="152">sed diam nonumy</text><text x="24" y="158">eirmod tempor</text>
      </g>
      <g fill="var(--bar-light)">
        <rect x="110" y="131.9" width="11" height="48.1"/><rect x="126.5" y="128.2" width="11" height="51.8"/>
        <rect x="143" y="117.1" width="11" height="62.9"/><rect x="159.5" y="102.3" width="11" height="77.7"/>
        <rect x="176" y="98.6" width="11" height="81.4"/><rect x="192.5" y="91.2" width="11" height="88.8"/>
        <rect x="209" y="83.8" width="11" height="96.2"/><rect x="225.5" y="76.4" width="11" height="103.6"/>
        <rect x="242" y="72.7" width="11" height="107.3"/><rect x="258.5" y="65.3" width="11" height="114.7"/>
        <rect x="275" y="61.6" width="11" height="118.4"/><rect x="291.5" y="54.2" width="11" height="125.8"/>
      </g>
      <g font-size="4.5" fill="#ffffff" text-anchor="middle">
        <text x="115.5" y="164">13</text><text x="132" y="164">14</text><text x="148.5" y="157">17</text>
        <text x="165" y="150">21</text><text x="181.5" y="148">22</text><text x="198" y="144">24</text>
        <text x="214.5" y="140">26</text><text x="231" y="136">28</text><text x="247.5" y="134">29</text>
        <text x="264" y="131">31</text><text x="280.5" y="129">32</text><text x="297" y="125">34</text>
      </g>
      <polyline fill="none" stroke="#9aa3ad" stroke-width="0.7"
        points="115.5,120.8 132,117.1 148.5,106 165,91.2 181.5,87.5 198,80.1 214.5,72.7 231,61.6 247.5,61.6 264,54.2 280.5,50.5 297,46.8"/>
      <g fill="#ffffff" stroke="#9aa3ad" stroke-width="0.7">
        <circle cx="115.5" cy="120.8" r="1.8"/><circle cx="132" cy="117.1" r="1.8"/><circle cx="148.5" cy="106" r="1.8"/>
        <circle cx="165" cy="91.2" r="1.8"/><circle cx="181.5" cy="87.5" r="1.8"/><circle cx="198" cy="80.1" r="1.8"/>
        <circle cx="214.5" cy="72.7" r="1.8"/><circle cx="231" cy="61.6" r="1.8"/><circle cx="247.5" cy="61.6" r="1.8"/>
        <circle cx="264" cy="54.2" r="1.8"/><circle cx="280.5" cy="50.5" r="1.8"/><circle cx="297" cy="46.8" r="1.8"/>
      </g>
      <g font-size="4.5" fill="var(--muted)" text-anchor="middle">
        <text x="115.5" y="116">16</text><text x="132" y="112">17</text><text x="148.5" y="101">20</text>
        <text x="165" y="86">24</text><text x="181.5" y="82">25</text><text x="198" y="75">27</text>
        <text x="214.5" y="67">29</text><text x="231" y="56">32</text><text x="247.5" y="56">32</text>
        <text x="264" y="49">34</text><text x="280.5" y="45">35</text><text x="297" y="42">36</text>
      </g>
      <text x="308" y="48" font-size="4.5" fill="var(--muted)">Lorem ipsum</text>
      <text x="308" y="106" font-size="4.5" fill="var(--bar-light)">Lorem ipsum</text>
      <text x="206" y="189" font-size="4.2" fill="var(--muted)" text-anchor="middle" letter-spacing="0.3">Text Text Text Text Text Text Text Text Text Text Text Text</text>
      <text x="350" y="200" font-size="3.5" fill="var(--muted)">31</text>
    </svg>
  </div>

  <div class="slide slide--ranking">
    <svg viewBox="0 0 366 206">
      <text x="183" y="18" font-size="11" font-weight="700" fill="var(--ink)" text-anchor="middle">Lorem ipsum dolor sit amet</text>
      <text x="183" y="31" font-size="6" fill="var(--ink)" text-anchor="middle">Lorem ipsum dolor sit amet, consectetuer adipiscing elit. Aenean commodo ligula eget dolor.</text>
      <text x="38" y="48" font-size="5.5" font-weight="700" fill="var(--ink)">Lorem ipsum</text>
      <text x="38" y="55" font-size="3.8" fill="var(--muted)">Lorem ipsum dolor sit amet, consetetur sadipscing elitr, sed diam nonumy eirmod tempor</text>
      <text x="38" y="60" font-size="3.8" fill="var(--muted)">invidunt ut labore et dolore magna aliquyam erat, sed diam voluptua. At vero eos et accusam.</text>
      <g font-size="3.8" fill="var(--muted)">
        <text x="24" y="73">Text</text><text x="24" y="84">Text</text><text x="24" y="95">Text</text><text x="24" y="106">Text</text><text x="24" y="117">Text</text>
        <text x="24" y="128">Text</text><text x="24" y="139">Text</text><text x="24" y="150">Text</text><text x="24" y="161">Text</text><text x="24" y="172">Text</text>
      </g>
      <g stroke="var(--grid)" stroke-width="0.4">
        <line x1="38" y1="76" x2="170" y2="76"/><line x1="38" y1="87" x2="170" y2="87"/><line x1="38" y1="98" x2="170" y2="98"/>
        <line x1="38" y1="109" x2="170" y2="109"/><line x1="38" y1="120" x2="170" y2="120"/><line x1="38" y1="131" x2="170" y2="131"/>
        <line x1="38" y1="142" x2="170" y2="142"/><line x1="38" y1="153" x2="170" y2="153"/><line x1="38" y1="164" x2="170" y2="164"/>
        <line x1="180" y1="76" x2="240" y2="76"/><line x1="180" y1="98" x2="240" y2="98"/><line x1="180" y1="120" x2="240" y2="120"/>
        <line x1="180" y1="142" x2="240" y2="142"/><line x1="180" y1="164" x2="240" y2="164"/>
      </g>
      <g fill="var(--bar-dark)">
        <rect x="38" y="69" width="93" height="5"/><rect x="38" y="80" width="87" height="5"/><rect x="38" y="91" width="84" height="5"/>
        <rect x="38" y="102" width="72" height="5"/><rect x="38" y="113" width="72" height="5"/><rect x="38" y="124" width="66" height="5"/>
        <rect x="38" y="135" width="63" height="5"/><rect x="38" y="146" width="51" height="5"/><rect x="38" y="157" width="42" height="5"/>
        <rect x="38" y="168" width="39" height="5"/>
      </g>
      <g font-size="3.8" fill="var(--ink)">
        <text x="134" y="73">31</text><text x="128" y="84">29</text><text x="125" y="95">28</text><text x="113" y="106">24</text>
        <text x="113" y="117">24</text><text x="107" y="128">22</text><text x="104" y="139">21</text><text x="92" y="150">17</text>
        <text x="83" y="161">14</text><text x="80" y="172">13</text>
      </g>
      <line x1="210" y1="66" x2="210" y2="176" stroke="#c5ccd3" stroke-width="0.4"/>
      <g fill="var(--bar-light)">
        <rect x="210" y="69" width="18" height="5"/><rect x="210" y="80" width="24" height="5"/><rect x="198" y="91" width="12" height="5"/>
        <rect x="204" y="102" width="6" height="5"/><rect x="210" y="113" width="18" height="5"/><rect x="210" y="124" width="18" height="5"/>
        <rect x="210" y="135" width="6" height="5"/><rect x="204" y="146" width="6" height="5"/><rect x="210" y="157" width="24" height="5"/>
        <rect x="210" y="168" width="12" height="5"/>
      </g>
      <g font-size="3.8" fill="var(--bar-light)">
        <text x="230" y="73">+3%</text><text x="236" y="84">+4%</text><text x="187" y="95">-2%</text><text x="193" y="106">-1%</text>
        <text x="230" y="117">+3%</text><text x="230" y="128">+3%</text><text x="218" y="139">+1%</text><text x="193" y="150">-1%</text>
        <text x="236" y="161">+4%</text><text x="224" y="172">+2%</text>
      </g>
      <g font-size="3.6" fill="var(--muted)">
        <text x="270" y="72">• Lorem ipsum dolor sit</text><text x="274" y="77">amet consetetur elit</text><text x="274" y="82">sed diam nonumy</text><text x="274" y="87">eirmod tempor</text>
        <text x="270" y="112">• Lorem ipsum dolor sit</text><text x="274" y="117">amet consetetur elit</text><text x="274" y="122">sed diam nonumy</text><text x="274" y="127">eirmod tempor</text>
        <text x="270" y="152">• Lorem ipsum dolor sit</text><text x="274" y="157">amet consetetur elit</text><text x="274" y="162">sed diam nonumy</text><text x="274" y="167">eirmod tempor</text>
      </g>
      <text x="350" y="200" font-size="3.5" fill="var(--muted)">33</text>
    </svg>
  </div>

  <h1 class="headline">Standard<br>Graphs</h1>
  <p class="subline">Slide Deck Presentation 1</p>
</div>
</body>
</html>
```